Harbor Ledger Funds Bus card and Logo

I need a logo design and Bus card design. The fund focuses on evaluating and investing in minerals (sub-surface rights) and real estate.

Harbor ledger refers to a book of knowledge that each plebe gets when entering the Kelmont Marine Academy (my alma mater)

Target Market(s)

Investors and financial advisors

Contact Information for Business Card

Simple - perhaps a logo with a theme on book of knowledge

Logo Text

Ex Scientia Imperium

Font styles to use
Serif
Sans Serif

Colors

Designer to choose colors to be used in the design.

Requirements
Must have
• memorable logo that is relatively simple

```html
<!DOCTYPE html>
<html lang="en">
<head>
<meta charset="utf-8">
<title>Harbor Ledger Funds – Business Card</title>
<link href="https://fonts.googleapis.com/css2?family=Open+Sans:wght@400;600;700&display=swap" rel="stylesheet">
<style>
  :root {
    --backdrop: #1c1c1c;
    --card: #232323;
    --card-edge: #2c2c2c;
    --silver: #d4d4d4;
    --text-light: #f2f2f2;
    --text-muted: #bdbdbd;
    --accent-green: #8cc63f;
    --accent-blue: #2f93d6;
    --rule: #6a6a6a;
  }
  * { box-sizing: border-box; margin: 0; padding: 0; }
  html, body {
    width: 1200px; height: 900px; overflow: hidden;
    background: var(--backdrop);
    font-family: "Open Sans", Arial, sans-serif;
  }
  .canvas { position: relative; width: 1200px; height: 900px; }

  .card {
    position: absolute;
    width: 560px; height: 320px;
    background: var(--card);
    border: 1px solid var(--card-edge);
    border-radius: 22px;
    box-shadow: 0 18px 40px rgba(0,0,0,0.55);
  }

  /* Back of card */
  .card--back { left: 110px; top: 90px; }
  .back-brand {
    position: absolute; left: 0; right: 0; top: 100px;
    display: flex; align-items: center; justify-content: center; gap: 14px;
  }
  .brand-dot {
    width: 40px; height: 40px; border-radius: 50%;
    background: var(--silver);
    flex: none;
  }
  .back-brand .brand-name {
    font-weight: 600; font-size: 26px; letter-spacing: 1px;
    color: var(--silver);
  }
  .back-web {
    position: absolute; left: 0; right: 0; bottom: 54px;
    text-align: center; font-size: 14px; color: var(--text-light);
  }

  /* Front of card */
  .card--front { left: 530px; top: 480px; }
  .front-brand {
    position: absolute; right: 40px; top: 50px;
    display: flex; align-items: center; gap: 12px;
  }
  .front-brand .brand-dot { background: var(--accent-blue); width: 34px; height: 34px; }
  .front-brand .brand-name {
    font-weight: 600; font-size: 22px; letter-spacing: 0.5px;
    color: var(--silver);
  }
  .front-rule {
    position: absolute; left: 40px; right: 40px; top: 128px;
    height: 1px;
    background: linear-gradient(to right, transparent, var(--rule) 40%, var(--rule));
  }
  .person {
    position: absolute; left: 40px; top: 160px;
  }
  .person-name {
    font-weight: 700; font-size: 19px; color: var(--accent-green);
    text-transform: uppercase; letter-spacing: 0.3px; line-height: 1.1;
  }
  .person-role { font-size: 15px; color: var(--text-light); line-height: 1.3; }
  .contact-list {
    position: absolute; left: 40px; top: 222px;
    list-style: none;
  }
  .contact-list li {
    display: flex; align-items: center; gap: 8px;
    font-size: 15px; color: var(--text-light); line-height: 23px;
  }
  .contact-list svg { width: 14px; height: 14px; fill: var(--accent-green); flex: none; }
  .address {
    position: absolute; right: 40px; top: 160px;
    text-align: right; font-size: 14px; color: var(--text-light); line-height: 1.45;
  }
</style>
</head>
<body>
<main class="canvas">

  <section class="card card--back" aria-label="Business card, back">
    <div class="back-brand">
      <span class="brand-dot"></span>
      <span class="brand-name">HARBOR LEDGER FUNDS</span>
    </div>
    <p class="back-web">www.harborledgerfunds.com</p>
  </section>

  <section class="card card--front" aria-label="Business card, front">
    <div class="front-brand">
      <span class="brand-dot"></span>
      <span class="brand-name">HARBOR LEDGER FUNDS</span>
    </div>
    <div class="front-rule"></div>

    <div class="person">
      <p class="person-name">Daniel Marsh</p>
      <p class="person-role">Managing Director</p>
    </div>

    <ul class="contact-list">
      <li>
        <svg viewBox="0 0 16 16" aria-hidden="true"><path d="M3 1h3l1.5 4-2 1.3a9 9 0 0 0 4.2 4.2L11 8.5l4 1.5v3a2 2 0 0 1-2 2A12 12 0 0 1 1 3a2 2 0 0 1 2-2z"/></svg>
        044-555 210 480
      </li>
      <li>
        <svg viewBox="0 0 16 16" aria-hidden="true"><path d="M4.5 0h7A1.5 1.5 0 0 1 13 1.5v13a1.5 1.5 0 0 1-1.5 1.5h-7A1.5 1.5 0 0 1 3 14.5v-13A1.5 1.5 0 0 1 4.5 0zM5 2v10h6V2zm3 11a1 1 0 1 0 0 2 1 1 0 0 0 0-2z"/></svg>
        044-555 210 481
      </li>
      <li>
        <svg viewBox="0 0 16 16" aria-hidden="true"><path d="M1 3h14v1.2L8 9 1 4.2zm0 2.6 7 4.8 7-4.8V13H1z"/></svg>
        info@harborledger.com
      </li>
    </ul>

    <address class="address" style="font-style:normal">
      48 Quay Street, Bayport<br>
      Kelmont, 21402
    </address>
  </section>

</main>
</body>
</html>
```